Letterhead Design for Law Firm

**Edit: I have added the photo of a bottom that I like.

------
We are looking for a re-design of our new letterhead. The letterhead is for a law firm and will be used for digital and traditionally printed correspondence.

Here are some suggestions:

- Please use colours are #8ec900 and simple black.
- Please do not use any type of "waves" at the bottom of the page. This is not in style at all.
- Please stay modern yet conservative.
- Please use font Segoe UI Light or similar if you can
- Avoid clipart or illustrations.
- Utilize ample white space in the layout so the design looks clean and information is easy to read at a glance. Don't overcrowd the letterhead.
- Make sure the letterhead design is consistent with our brand identity (see corvelith.ca)
-Please, no black headers or footers.

I am attaching my current letterhead and signature for your convenience.

Remember, the letterhead is an extension of our professional identity. We are a successful firm and trial lawyers who correspond with insurers, judges, lawyers, courts, clients, etc. Make it new, modern, attractive, yet powerful and conservative.

It needs to be easily printable. I would like the bleed removed in print so the black bar the bottom crosses the page (but the text is not near the edges)
Updates

Low design quality

Target Market(s)

Clients, Government Offices, Judiciary, Lawyers, Insurance Companies, Colleagues.

Industry/Entity Type

Law

Other font styles liked:
• Segoe UI LIght, Calibri Light,

Colors
00AB8E
00BBA5
67D7C9
C6EFE9
E9F9F6

Requirements
Must have
• Everything that is on the letterhead now.
Nice to have
• Cutting Edge design, yet conservative.
Should not have
• law firm cliche design, images,

```html
<!DOCTYPE html>
<html lang="en">
<head>
<meta charset="utf-8">
<title>Marlowe Personal Injury Lawyers – Letterhead</title>
<link rel="stylesheet" href="https://fonts.googleapis.com/css2?family=Open+Sans:wght@400;600;700&display=swap">
<style>
  :root {
    --brand-green: #8cc34b;
    --ink: #1e1e1e;
    --ink-soft: #2b2b2b;
    --paper: #faf9fa;
    --backdrop: #e9e8e6;
    --signature-tone: #d9d7d8;
  }
  * { box-sizing: border-box; margin: 0; padding: 0; }
  html, body {
    width: 1200px; height: 1111px; overflow: hidden;
    background: var(--backdrop);
    font-family: "Open Sans", "Segoe UI", sans-serif;
    color: var(--ink);
  }
  .letterhead {
    position: absolute; left: 169px; top: 0;
    width: 862px; height: 1111px;
    background: var(--paper);
    overflow: hidden;
  }
  .abs { position: absolute; white-space: nowrap; }

  /* Brand block */
  .brand-name {
    left: 46px; top: 40px;
    font-size: 62px; font-weight: 700; letter-spacing: 1px;
    line-height: 70px; color: var(--ink);
  }
  .brand-tagline {
    left: 50px; top: 112px;
    font-size: 15.5px; font-weight: 400; letter-spacing: 2.2px;
    color: var(--ink);
  }

  /* Contact column */
  .contact-rule {
    left: 637px; top: 49px; width: 2.5px; height: 216px;
    background: var(--brand-green);
  }
  .contact {
    left: 649px; top: 46px; font-style: normal;
    font-size: 11.4px; line-height: 16.1px; color: var(--ink-soft);
  }
  .contact strong { font-weight: 700; }
  .contact .web-accent { color: var(--brand-green); font-weight: 600; }
  .contact .gap { height: 16px; }

  /* Letter body */
  .letter-text { font-size: 14px; line-height: 19.4px; color: var(--ink); }
  .label { font-weight: 600; }
  .prejudice { left: 60px; top: 158px; }
  .date { left: 60px; top: 197px; }
  .delivery { left: 60px; top: 236px; }
  .recipient { left: 60px; top: 275px; }
  .attention { left: 60px; top: 391px; }
  .salutation { left: 60px; top: 430px; }
  .re-label { left: 60px; top: 468px; }
  .re-detail { left: 269px; top: 468px; font-weight: 600; }
  .re-detail sup { font-size: 9px; line-height: 0; vertical-align: 5px; }
  .re-rule {
    left: 58px; top: 530px; width: 682px; height: 1px;
    background: var(--ink);
  }

  /* Closing */
  .closing { left: 60px; top: 760px; }
  .closing .firm { font-weight: 600; }
  .signature {
    left: 60px; top: 814px; width: 200px; height: 46px;
    background: var(--signature-tone); border-radius: 3px;
  }
  .signer { left: 60px; top: 862px; font-size: 14px; line-height: 19px; }
  .signer-meta {
    left: 60px; top: 882px;
    font-size: 11.6px; line-height: 16.2px;
  }
  .signer-meta .corp { font-weight: 600; }

  /* Footer: clean straight rule and full-bleed green bar */
  .footer-rule {
    left: 0; top: 1046px; width: 862px; height: 2px;
    background: var(--ink);
  }
  .footer-bar {
    left: 0; top: 1056px; width: 862px; height: 55px;
    background: var(--brand-green);
  }
</style>
</head>
<body>
  <main class="letterhead">
    <div class="abs brand-name">MARLOWE</div>
    <div class="abs brand-tagline">PERSONAL INJURY LAWYERS</div>

    <div class="abs contact-rule"></div>
    <address class="abs contact">
      <div>www.<span class="web-accent">CORVELITH</span>.ca</div>
      <div>48 Elmview Street W., Suite 1210</div>
      <div>Hamilton, ON&nbsp; L8P 3K2</div>
      <div><strong>T:</strong> 905-555-0142</div>
      <div><strong>F:</strong> 905-555-0179</div>
      <div><strong>File Clerk:</strong> Nora Whitcombe</div>
      <div><strong>Email:</strong> nora@corvelith.ca</div>
      <div class="gap"></div>
      <div><strong>Practice Restricted</strong></div>
      <div>Serious Personal Injury</div>
      <div>Wrongful Death Litigation</div>
      <div>Long-Term Disability Litigation</div>
      <div>Wrongful Dismissal Litigation</div>
      <div>Employee Terminations</div>
    </address>

    <div class="abs letter-text prejudice label">Without Prejudice</div>
    <div class="abs letter-text date">March 13, 2024</div>
    <div class="abs letter-text delivery label">By Email</div>
    <div class="abs letter-text recipient">
      <div>Northmere Insurance Company</div>
      <div>Claims Litigation Department</div>
      <div>240 Ridgeline Road South</div>
      <div>P.O. Box 4100</div>
      <div>Kitchener, ON&nbsp;&nbsp; N2G 1H6</div>
    </div>
    <div class="abs letter-text attention">Attention:&nbsp; Mr. Dalen Price</div>
    <div class="abs letter-text salutation">Mr. Price:</div>

    <div class="abs letter-text re-label label">Re:</div>
    <div class="abs letter-text re-detail">
      <div>Hartley v. Osborne et al.</div>
      <div>DOL:&nbsp; September 12, 2019</div>
      <div>Pre-Mediation Settlement Proposal – March 13<sup>th</sup>, 2024</div>
    </div>
    <div class="abs re-rule"></div>

    <div class="abs letter-text closing">
      <div>Yours very truly,</div>
      <div class="firm">MARLOWE PERSONAL INJURY LAWYERS</div>
    </div>
    <div class="abs signature" role="img" aria-label="Handwritten signature of Owen T. Marlowe"></div>
    <div class="abs signer">Owen T. Marlowe</div>
    <div class="abs signer-meta">
      <div class="corp">Marlowe Law Professional Corporation</div>
      <div>/nw</div>
      <div>Encl.</div>
    </div>

    <div class="abs footer-rule"></div>
    <div class="abs footer-bar"></div>
  </main>
</body>
</html>
```